Business card design for a dynamic IT consulting company

We need a business card design for a young firm, specialized in the Telecommunications/Consulting industry. The name of the company is Quindor and Partners Business Consulting Ltd. (Short name: Quindor and Partnes)
Quindor = solve read reverse, so we aim to be uncomplicated and solution-oriented. The small pipe in our logo is also related to the word solve. So we need a new business card design, which is simple, eye catching and something non traditional (I would probably prefer a square shaped design rather than a rectangle, but open for suggestions). Attached our logo.

Target Market(s)

Usually our customers are Tier1 Telecoms providers (Q-Netra, Palorix, etc) and their executives.

Industry/Entity Type

Business

Contact Information for Business Card

Name: Bence Tolnavari
Email: b.tolnavari@quindor.hu
Web: www.quindor.hu
Mobile: +36 30 518 2769
Title: Managing Director

Optional:
Company name: Quindor and Partners Ltd.
Address: 1087 Budapest, Tolvenka str. 28/C, Hungary

Font styles to use
Other font styles liked:
• helveticaneue_medium, Prime Regular are used now.

Colors

Designer to choose colors to be used in the design.

Requirements
Must have
• I would like to have a 2 sided design.
Nice to have
• I thought if we make the logo a bit bigger (without the company name), that could go to the back with the company name below. I though, if the pipe in the logo is somehow touchable on the business card, would be nice and unique.

```html
<!DOCTYPE html>
<html lang="en">
<head>
<meta charset="utf-8">
<title>Quindor and Partners – Business Card</title>
<link rel="stylesheet" href="https://fonts.googleapis.com/css2?family=Arimo:wght@400;700&display=swap">
<style>
  :root {
    --backdrop: #5b4838;
    --card-edge: #58585a;
    --card-face: #f1f1f1;
    --ink: #4a4a4c;
    --ink-soft: #5c5c5e;
    --accent-blue: #1490d2;
    --accent-magenta: #b4307e;
    --tint-blue: rgba(20, 144, 210, 0.12);
    --tint-magenta: rgba(180, 48, 126, 0.10);
    --tint-grey: rgba(88, 88, 90, 0.10);
  }
  * { margin: 0; padding: 0; box-sizing: border-box; }
  html, body {
    width: 1200px; height: 960px; overflow: hidden;
    background: var(--backdrop);
    font-family: "Arimo", Arial, sans-serif;
  }
  .canvas { position: relative; width: 1200px; height: 960px; }
  .card {
    position: absolute; top: 309px;
    width: 343px; height: 343px;
    background: var(--card-edge);
    padding: 12px;
  }
  .card--front { left: 235px; }
  .card--back { left: 623px; }
  .card__face {
    position: relative;
    width: 100%; height: 100%;
    background: var(--card-face);
    display: flex; flex-direction: column; align-items: center;
    text-align: center; color: var(--ink);
  }
  .card--front .card__face { padding-top: 74px; }
  .backdrop-pattern {
    position: absolute; left: 16px; top: 51px;
    width: 288px; height: 216px;
    background: linear-gradient(135deg, var(--tint-magenta), var(--tint-blue) 55%, var(--tint-grey));
  }
  .card__content { position: relative; display: flex; flex-direction: column; align-items: center; }
  .person__name {
    font-weight: 700; font-size: 18px; color: var(--accent-blue);
    letter-spacing: 0.2px; line-height: 22px;
  }
  .person__title {
    font-size: 15px; color: var(--ink-soft); letter-spacing: 0.4px;
    line-height: 20px;
  }
  .company {
    margin-top: 8px; font-style: normal;
    font-size: 14px; line-height: 18px; color: var(--ink-soft);
  }
  .contact { margin-top: 10px; list-style: none; font-size: 14px; line-height: 18px; color: var(--ink-soft); }
  .contact li { display: flex; align-items: center; justify-content: center; gap: 3px; }
  .contact svg { width: 11px; height: 11px; fill: var(--accent-blue); }
  .card--back .card__face { padding-top: 84px; }
  .brand__mark {
    width: 76px; height: 76px;
    background: var(--tint-grey);
  }
  .brand {
    margin-top: 14px;
    font-size: 30px; font-weight: 400; color: var(--ink);
    letter-spacing: 0.3px; line-height: 34px;
  }
</style>
</head>
<body>
<main class="canvas">
  <section class="card card--front" aria-label="Card front">
    <div class="card__face">
      <div class="backdrop-pattern" role="img" aria-label="Faint coloured background pattern in magenta, blue and grey"></div>
      <div class="card__content">
        <h1 class="person__name">BENCE TOLNAVARI</h1>
        <p class="person__title">MANAGING DIRECTOR</p>
        <address class="company">
          Quindor and Partners Ltd.<br>
          1087 Budapest<br>
          Tolvenka str. 28/C, Hungary
        </address>
        <ul class="contact">
          <li><svg viewBox="0 0 12 12" aria-hidden="true"><path d="M3 0h6a1 1 0 0 1 1 1v10a1 1 0 0 1-1 1H3a1 1 0 0 1-1-1V1a1 1 0 0 1 1-1zm0 1.5v8h6v-8z"/></svg>+36 30 518 2769</li>
          <li><svg viewBox="0 0 12 12" aria-hidden="true"><path d="M0 2h12v8H0zm1 1 5 4 5-4z"/></svg>b.tolnavari@quindor.hu</li>
          <li><svg viewBox="0 0 12 12" aria-hidden="true"><circle cx="6" cy="6" r="6"/></svg>www.quindor.hu</li>
        </ul>
      </div>
    </div>
  </section>
  <section class="card card--back" aria-label="Card back">
    <div class="card__face">
      <span class="brand__mark" role="img" aria-label="Company mark area"></span>
      <p class="brand">Quindor &amp; Partners</p>
    </div>
  </section>
</main>
</body>
</html>
```